One piece Trade show banner, 8' x 8' square

One piece banner for trade show
8' x 8' airborne geophysical company

Target Market(s)

Business

Industry/Entity Type

mineral exploration and science

Colors
0054AA
0677BA
7BADD7
CADEEF
E8F1F8
FFC000
F8CF3A
FAE287
FDF2CF
FEFAEE

Requirements
Must have
• Company logo (attached), slogan (Airborne Geophysics for Discovery). We are looking for a new banner, for a standard 8 x 8' square one-piece booth. I have attached some pictures, our logo, our old banner for reference, and two examples from unrelated companies from a tradeshow that we like. If its possible I'd like to change the color of the helicopter from green to dark grey. IE, keep the orange and white, just change green to dark grey. Looking for a simple, clean design with minimal text.
Nice to have
• I have attached examples of banners that we like (2xIMG), plus our old 3-piece banner r.
Should not have
• Green in the helicopter. Please change the color of the helicopter with green/orange/white to dark grey/orange/white. IE change the green to dark grey and leave the orange and white alone. I've attached lots of pictures but I don't expect them all to be used.

```html
<!DOCTYPE html>
<html lang="en">
<head>
<meta charset="utf-8">
<title>Summit AeroSurveys – Trade Show Banner</title>
<link rel="stylesheet" href="https://fonts.googleapis.com/css2?family=Archivo+Black&family=Poppins:wght@400;600&display=swap">
<style>
  :root {
    --page: #ececec;
    --night: #14171b;
    --night-soft: #2a3036;
    --gold: #ffc000;
    --gold-light: #fae287;
    --gold-deep: #b98a00;
    --white: #ffffff;
    --sky: #cadeef;
    --lake: #0677ba;
  }
  * { margin: 0; padding: 0; box-sizing: border-box; }
  html, body {
    width: 927px; height: 1200px; overflow: hidden;
    background: var(--page);
  }
  .banner {
    position: absolute; left: 0; top: 136px;
    width: 927px; height: 927px; overflow: hidden;
    background: var(--night);
  }
  .banner__art { position: absolute; inset: 0; width: 927px; height: 927px; }
  .brand {
    position: absolute; right: 42px; top: 52px;
    text-align: right; color: var(--white);
    font-family: "Poppins", sans-serif; font-weight: 400; line-height: 1;
  }
  .brand__name { display: block; font-size: 64px; letter-spacing: -1px; }
  .brand__tag { display: block; font-size: 26px; margin-top: 2px; }
  .headline {
    position: absolute; right: 42px; top: 480px;
    text-align: right; color: var(--gold);
    font-family: "Archivo Black", sans-serif; font-size: 51px;
    line-height: 60px; text-transform: uppercase; letter-spacing: 1px;
  }
  .services {
    position: absolute; right: 42px; top: 668px;
    text-align: right; color: var(--gold);
    font-family: "Poppins", sans-serif; font-weight: 600;
    font-size: 27px; line-height: 40px;
  }
  .services__item + .services__item { margin-left: 26px; }
  .website {
    position: absolute; left: 48px; top: 835px;
    display: flex; align-items: center; gap: 8px;
    color: var(--gold);
    font-family: "Poppins", sans-serif; font-weight: 600; font-size: 27px;
  }
</style>
</head>
<body>
  <main class="banner">
    <svg class="banner__art" viewBox="0 0 927 927" xmlns="http://www.w3.org/2000/svg">
      <defs>
        <linearGradient id="backdrop" x1="0" y1="0" x2="1" y2="1">
          <stop offset="0" stop-color="#1b2025"/>
          <stop offset="0.6" stop-color="#2a3036"/>
          <stop offset="1" stop-color="#15181c"/>
        </linearGradient>
        <linearGradient id="gold-ring" x1="0" y1="0" x2="1" y2="1">
          <stop offset="0" stop-color="#ffc000"/>
          <stop offset="0.5" stop-color="#f8cf3a"/>
          <stop offset="0.8" stop-color="#c99600"/>
          <stop offset="1" stop-color="#ffc000"/>
        </linearGradient>
        <linearGradient id="photo-main" x1="0" y1="0" x2="0" y2="1">
          <stop offset="0" stop-color="#e8f1f8"/>
          <stop offset="0.4" stop-color="#9fb6c8"/>
          <stop offset="0.65" stop-color="#6f8f7a"/>
          <stop offset="1" stop-color="#4f7a45"/>
        </linearGradient>
        <linearGradient id="photo-peak" x1="0" y1="0" x2="1" y2="0">
          <stop offset="0" stop-color="#9a5a2a"/>
          <stop offset="0.6" stop-color="#7a4a2c"/>
          <stop offset="1" stop-color="#7badd7"/>
        </linearGradient>
        <linearGradient id="photo-lake" x1="0" y1="0" x2="0" y2="1">
          <stop offset="0" stop-color="#8a8a82"/>
          <stop offset="0.45" stop-color="#5f6d70"/>
          <stop offset="0.6" stop-color="#0677ba"/>
          <stop offset="1" stop-color="#0054aa"/>
        </linearGradient>
      </defs>

      <rect class="backdrop" width="927" height="927" fill="url(#backdrop)"
            role="img" aria-label="Dark aerial photo of snowy rock terrain with a survey helicopter"/>

      <circle class="gold-disc" cx="259" cy="376" r="380" fill="url(#gold-ring)"/>

      <g class="photo photo--main">
        <circle cx="259" cy="247" r="250" fill="#1a1a1a"/>
        <circle cx="259" cy="247" r="243" fill="var(--white)"/>
        <circle cx="259" cy="247" r="232" fill="url(#photo-main)"
                role="img" aria-label="Dark grey helicopter flying over green valley and mountains"/>
      </g>

      <g class="photo photo--peak">
        <circle cx="470" cy="397" r="130" fill="var(--gold)"/>
        <circle cx="470" cy="397" r="125" fill="var(--white)"/>
        <circle cx="470" cy="397" r="119" fill="url(#photo-peak)"
                role="img" aria-label="Helicopter with survey boom beside a rocky mountain peak"/>
      </g>

      <g class="photo photo--lake">
        <circle cx="211" cy="569" r="147" fill="#1a1a1a"/>
        <circle cx="211" cy="569" r="141" fill="var(--white)"/>
        <circle cx="211" cy="569" r="134" fill="url(#photo-lake)"
                role="img" aria-label="White and orange helicopter over a blue mountain lake"/>
      </g>

      <line class="brand-rule" x1="590" y1="66" x2="885" y2="66" stroke="var(--gold)" stroke-width="1.5"/>
    </svg>

    <div class="brand">
      <span class="brand__name">Summit</span>
      <span class="brand__tag">AeroSurveys</span>
    </div>

    <h1 class="headline">Airborne<br>Geophysics<br>for Discovery</h1>

    <p class="services">
      <span class="services__item">Helicopter</span><span class="services__item">Fixed Wing</span><span class="services__item">Drone</span><br>
      Exploring Nevada since 2007
    </p>

    <div class="website">
      <svg class="website__icon" width="58" height="58" viewBox="0 0 58 58" aria-hidden="true">
        <g fill="none" stroke="var(--gold)" stroke-width="3">
          <circle cx="29" cy="29" r="26"/>
          <ellipse cx="29" cy="29" rx="12" ry="26"/>
          <line x1="29" y1="3" x2="29" y2="55"/>
          <line x1="3" y1="29" x2="55" y2="29"/>
          <path d="M7 16 H51 M7 42 H51"/>
        </g>
      </svg>
      <span class="website__url">www.summitaerosurveys.com</span>
    </div>
  </main>
</body>
</html>
```